Social Media Graphics - Oakline Push REVISED

Create 6-7 individual social media graphics (square size) to encourage folks to join our online course called:

The Harvest Ledger Circle
How to Launch a Multi-Million Business From Scratch
Sign Up Today!

IMPORTANT: Make the largest and most prominent text on the graphic be: How to Launch a Multi-Million Business From Scratch

For the color scheme of the graphics, let's try a blue color palette; make sure the graphics appeal to both men and women

Make sure each graphic contains 1 of the 3 pics attached (crop pic as needed); and make sure one of the graphics is all TEXT only.

Target Market(s)

men and women looking to start a business

Industry/Entity Type

Entrepreneurship

Colors
0054AA
0677BA
7BADD7
CADEEF
E8F1F8

Requirements
Must have
• All the text and use the 3 pics provided; one graphic can be all text; Simple, modern design that's easy to read

```html
<!DOCTYPE html>
<html lang="en">
<head>
<meta charset="utf-8">
<title>The Harvest Ledger Circle – Social Graphic</title>
<link href="https://fonts.googleapis.com/css2?family=Anton&family=Bebas+Neue&family=Montserrat:wght@600;700;800&display=swap" rel="stylesheet">
<style>
  :root {
    --stage: #64a2c6;
    --blue-deep: #0b3a94;
    --blue-main: #1b56b8;
    --blue-bright: #2a6ad0;
    --blue-text: #0054aa;
    --pink: #ee2f5c;
    --white: #ffffff;
    --photo-warm: #c9b9a4;
    --photo-mid: #6d6e86;
  }
  * { margin: 0; padding: 0; box-sizing: border-box; }
  html, body { width: 1200px; height: 862px; overflow: hidden; }
  body {
    background: var(--stage);
    display: flex; align-items: center; justify-content: center;
    font-family: "Montserrat", sans-serif;
  }
  .post {
    position: relative;
    width: 780px; height: 780px;
    overflow: hidden;
    background: linear-gradient(160deg, var(--blue-bright) 0%, var(--blue-main) 45%, var(--blue-deep) 100%);
    box-shadow: 0 28px 40px rgba(20, 50, 90, 0.35);
  }
  .post__photo {
    position: absolute; inset: 0 0 auto 0; height: 560px;
    background:
      linear-gradient(180deg, rgba(27,86,184,0) 0%, rgba(27,86,184,0) 45%, rgba(27,86,184,0.85) 80%, var(--blue-main) 100%),
      linear-gradient(180deg, var(--photo-warm) 0%, #a89a8c 30%, var(--photo-mid) 60%, #3d5c9e 100%);
  }
  .post__title {
    position: absolute; top: 30px; left: 0; right: 0;
    text-align: center;
    font-family: "Bebas Neue", "Oswald", sans-serif;
    font-size: 66px; letter-spacing: 1px; line-height: 1;
    color: var(--white);
    text-shadow: 2px 3px 4px rgba(0,0,0,0.55);
  }
  .pill {
    position: absolute; left: 50%;
    display: flex; align-items: center; justify-content: center;
    border-radius: 40px; white-space: nowrap;
  }
  .pill--howto {
    top: 322px; width: 240px; height: 58px;
    transform: translateX(-60%) rotate(-4deg);
    background: var(--white); color: var(--blue-text);
    font-weight: 600; font-size: 46px;
    box-shadow: 0 4px 8px rgba(0,0,0,0.25);
  }
  .pill--launch {
    top: 380px; width: 320px; height: 50px;
    transform: translateX(-45%);
    background: var(--pink); color: var(--white);
    font-weight: 600; font-size: 44px; letter-spacing: 1px;
    box-shadow: 0 4px 8px rgba(0,0,0,0.25);
  }
  .headline {
    position: absolute; top: 432px; left: 0; right: 0;
    text-align: center;
    font-family: "Anton", sans-serif;
    font-size: 96px; line-height: 1; letter-spacing: 1px;
    color: var(--white);
    text-shadow: 3px 4px 5px rgba(0,0,0,0.45);
  }
  .subline {
    position: absolute; top: 536px; left: 0; right: 0;
    text-align: center;
    font-weight: 800; font-size: 58px; line-height: 1;
    color: var(--white);
    text-shadow: 2px 3px 4px rgba(0,0,0,0.35);
  }
  .pill--scratch {
    top: 613px; width: 520px; height: 64px;
    transform: translateX(-50%);
    border: 2px solid var(--white);
    color: var(--white);
    font-weight: 700; font-size: 53px;
  }
  .pill--cta {
    top: 696px; width: 222px; height: 46px;
    transform: translateX(-50%);
    background: var(--pink); color: var(--white);
    border: 2px solid var(--white);
    font-weight: 700; font-size: 20px; letter-spacing: 0.5px;
    box-shadow: 0 4px 8px rgba(0,0,0,0.3);
  }
  .chevrons { position: absolute; width: 34px; height: 66px; }
  .chevrons--down { left: 28px; top: 314px; }
  .chevrons--up { right: 16px; top: 553px; }
  .ring { position: absolute; left: 705px; top: 702px; }
</style>
</head>
<body>
  <main class="post">
    <div class="post__photo" role="img" aria-label="Photo of a smiling woman and man presenting on stage with microphones in a bright conference room"></div>

    <h1 class="post__title">The Harvest Ledger Circle</h1>

    <svg class="chevrons chevrons--down" viewBox="0 0 34 66" aria-hidden="true">
      <g fill="none" stroke="#fff" stroke-width="4" stroke-linejoin="round">
        <polyline points="3,4 17,16 31,4"/>
        <polyline points="3,20 17,32 31,20"/>
        <polyline points="3,36 17,48 31,36"/>
        <polyline points="3,52 17,64 31,52"/>
      </g>
    </svg>

    <div class="pill pill--howto">HOW TO</div>
    <div class="pill pill--launch">LAUNCH A</div>
    <p class="headline">MULTI-MILLION</p>
    <p class="subline">BUSINESS</p>
    <div class="pill pill--scratch">FROM SCRATCH</div>
    <div class="pill pill--cta">SIGN UP TODAY!</div>

    <svg class="chevrons chevrons--up" viewBox="0 0 34 66" aria-hidden="true">
      <g fill="none" stroke="#fff" stroke-width="4" stroke-linejoin="round">
        <polyline points="3,14 17,2 31,14"/>
        <polyline points="3,30 17,18 31,30"/>
        <polyline points="3,46 17,34 31,46"/>
        <polyline points="3,62 17,50 31,62"/>
      </g>
    </svg>

    <svg class="ring" width="30" height="30" viewBox="0 0 30 30" aria-hidden="true">
      <circle cx="15" cy="15" r="12" fill="none" stroke="#2a86e0" stroke-width="2.5"/>
    </svg>
  </main>
</body>
</html>
```